Business cards for Zestcycle

We need a business card layout for our new bike and e-bike rental (we also sell used e-bikes and bike accessories). The logo already exists.

```html
<!DOCTYPE html>
<html lang="de">
<head>
<meta charset="utf-8">
<title>Zestcycle – Business Cards</title>
<link rel="stylesheet" href="https://fonts.googleapis.com/css2?family=Open+Sans:wght@400;600&family=Cabin:wght@500&display=swap">
<style>
  :root {
    --backdrop: #2e2e2e;
    --card-light: #eeeeee;
    --mint: #5fc3a6;
    --ink: #1f2d33;
    --white: #ffffff;
    --rule: #a9a9a9;
  }
  * { margin: 0; padding: 0; box-sizing: border-box; }
  html, body { width: 1200px; height: 1200px; overflow: hidden; }
  body {
    background: var(--backdrop);
    position: relative;
    font-family: "Open Sans", Arial, sans-serif;
    color: var(--ink);
  }
  .card {
    position: absolute;
    top: 310px;
    height: 594px;
    text-align: center;
    box-shadow: 0 4px 14px rgba(0,0,0,0.45);
  }
  .card--front { left: 234px; width: 364px; background: var(--card-light); }
  .card--back { left: 627px; width: 369px; background: var(--mint); }

  .brand-name {
    position: absolute;
    left: 0; right: 0;
    font-weight: 400;
    letter-spacing: 1px;
    line-height: 1;
  }
  .card--front .brand-name { top: 160px; font-size: 60px; color: var(--mint); }
  .card--back .brand-name { top: 288px; font-size: 60px; color: var(--ink); }

  .tagline {
    position: absolute;
    left: 0; right: 0;
    font-family: "Cabin", "Open Sans", sans-serif;
    font-weight: 500;
    font-size: 21px;
  }
  .card--front .tagline { top: 255px; color: var(--ink); }
  .card--back .tagline { top: 373px; color: var(--white); }

  .contact { position: absolute; top: 334px; left: 0; right: 0; }
  .contact__name { font-size: 22px; font-weight: 400; line-height: 1.1; letter-spacing: 0.3px; }
  .contact__role { font-size: 17px; line-height: 1.25; }
  .contact__rule { width: 208px; height: 1px; background: var(--rule); margin: 6px auto 12px; }
  .contact__lines { font-size: 17px; line-height: 21.5px; }
  .contact__lines b { font-weight: 600; }
  .contact__web { font-weight: 600; }
  .contact__web span { color: var(--mint); font-weight: 400; }
  .contact__rule--lower { margin-top: 11px; margin-bottom: 7px; }
  .contact__address { font-size: 17px; line-height: 21.5px; }

  .services {
    position: absolute;
    top: 505px; left: 0; right: 0;
    font-size: 15.8px;
    line-height: 19px;
    color: var(--ink);
    text-transform: uppercase;
  }
</style>
</head>
<body>
  <section class="card card--front">
    <div class="brand-name">ZESTCYCLE</div>
    <div class="tagline">mit Schwung unterwegs</div>
    <div class="contact">
      <div class="contact__name">MARTIN KELLER</div>
      <div class="contact__role">Managing Director</div>
      <div class="contact__rule"></div>
      <div class="contact__lines">
        <div><b>P:</b> 044-555 210 340</div>
        <div><b>M:</b> 079-555 418 226</div>
        <div><b>E:</b> hello@zestcycle.ch</div>
        <div class="contact__web">www.<span>zestcycle</span>.ch</div>
      </div>
      <div class="contact__rule contact__rule--lower"></div>
      <div class="contact__address">
        <div>Seestrasse 48, 8002 Zürich</div>
        <div>Switzerland</div>
      </div>
    </div>
  </section>

  <section class="card card--back">
    <div class="brand-name">ZESTCYCLE</div>
    <div class="tagline">mit Schwung unterwegs</div>
    <div class="services">
      <div>New bike and e-bike rental</div>
      <div>Sell used e-bikes and bike accessories</div>
    </div>
  </section>
</body>
</html>
```